Website for Torvel Capital - investment banking firm

We have a corporate identity (thanks to Ravinka/31842) and want to extend that into a website design.  See the attached zipped files.
We have software folks in-house to do the coding.
See the attached Project Brief & Notes for more details.  Don't worry about the actual text - lorem ipsum will be fine.
The server will be Apache.
Thank you!
Desmond

Industry/Entity Type
Investment

```html
<!DOCTYPE html>
<html lang="en">
<head>
<meta charset="utf-8">
<title>Torvel Capital</title>
<link href="https://fonts.googleapis.com/css2?family=Open+Sans:wght@400;600;700&display=swap" rel="stylesheet">
<style>
:root{
  --blue:#0d3f7f;
  --navy:#083370;
  --grey-tab:#8a8a8a;
  --text:#222;
  --red:#a50f12;
  --panel:#f0f0f0;
  --footer:#2c2c2c;
}
*{margin:0;padding:0;box-sizing:border-box}
html,body{width:853px;height:1200px;overflow:hidden;font-family:"Open Sans",sans-serif;color:var(--text);background:#fff}
.page{position:relative;width:853px;height:1200px}
.abs{position:absolute}
.header{left:0;top:0;width:853px;height:108px;background:repeating-linear-gradient(135deg,#f6f6f6 0 2px,#fbfbfb 2px 4px)}
.brand{left:79px;top:16px;display:flex;align-items:center;gap:12px;height:46px}
.brand-square{width:40px;height:40px;background:var(--blue)}
.brand-name{font-family:"Open Sans",sans-serif;font-weight:600;font-size:30px;color:var(--blue);line-height:46px}
.contact-top{left:670px;top:14px;color:var(--blue);font-weight:600;font-size:11.5px;line-height:21px}
.contact-top svg{position:absolute;left:0;top:6px}
.contact-top div{padding-left:30px}
.nav{left:80px;top:83px;display:flex;gap:2px}
.nav a{display:block;height:24px;line-height:24px;text-align:center;font-size:10.5px;color:#fff;text-decoration:none;background:var(--navy);border-radius:3px 3px 0 0}
.nav a.active{background:var(--grey-tab)}
.hero{left:0;top:108px;width:853px;height:292px;background:linear-gradient(180deg,#c6d3df 0%,#dde4ea 40%,#9aa4ad 75%,#6d7680 100%)}
.hero-caption{left:79px;top:194px;width:250px;height:113px;background:rgba(70,70,70,.7);border-radius:3px;padding:18px 20px;color:#fff;font-size:12.2px;line-height:25.5px;text-align:justify}
.dots{left:362px;top:377px;width:128px;height:23px;background:#3a3a3a;clip-path:polygon(10% 0,90% 0,100% 100%,0 100%);display:flex;justify-content:center;align-items:center;gap:9px}
.dots span{width:9px;height:9px;border-radius:50%;background:#222;border:1px solid #555}
.dots span.on{background:#1a6fd1}
.services{left:0;top:404px;width:853px;height:229px;background:linear-gradient(180deg,#fff 0%,#ececec 100%)}
.h2{font-size:18px;font-weight:400;color:#111}
.svc{width:152px}
.svc h3{font-size:13.5px;font-weight:700;color:var(--blue);line-height:22px;margin-bottom:11px}
.svc p{font-size:8.9px;line-height:12.8px;text-align:justify;hyphens:auto;-webkit-hyphens:auto;padding-left:2px;letter-spacing:-.1px}
.svc a{display:block;margin-top:6px;font-size:9px;font-weight:700;color:var(--red);text-decoration:none;padding-left:3px}
.welcome-h{left:86px;top:665px;font-size:17px;width:385px;padding-bottom:4px;border-bottom:1px solid #e3e3e3}
.welcome-h b,.who-h b{color:var(--blue);font-weight:400}
.welcome-p{left:88px;top:702px;width:385px;font-size:8.2px;line-height:15px}
.btn{left:415px;top:751px;width:66px;height:23px;background:var(--navy);color:#fff;font-size:7px;font-weight:700;line-height:23px;text-align:center}
.map{left:525px;top:675px;width:217px;height:112px;background:radial-gradient(ellipse at center,#8ea4c9 0%,#b7c6de 60%,rgba(255,255,255,0) 75%)}
.who{left:0;top:820px;width:853px;height:271px;background:var(--panel)}
.who-h{left:86px;top:829px;font-size:17px}
.tabs{left:80px;top:866px;display:flex;gap:3px}
.tabs span{display:block;height:32px;line-height:36px;text-align:center;font-size:13px;font-weight:600;color:var(--blue);background:#e0e0e0;border-radius:3px 3px 0 0}
.tabs span.on{background:#ececec}
.tab-panel{left:80px;top:898px;width:685px;height:176px;background:linear-gradient(90deg,#ececec,#f4f4f4);border-radius:0 3px 3px 3px;box-shadow:0 1px 2px rgba(0,0,0,.1)}
.tab-text{left:95px;top:929px;width:655px;font-size:8.2px;line-height:15px}
.clients{left:105px;top:1010px;width:650px;display:flex;justify-content:space-between;align-items:center}
.clients span{font-size:9.5px;font-weight:600;color:#777}
.footer{left:0;top:1091px;width:853px;height:109px;background:var(--footer);color:#ddd}
.footer h4{position:absolute;left:80px;top:10px;font-size:13px;font-weight:400;color:#fff}
.f-addr{left:112px;top:38px;width:110px;font-size:8.4px;line-height:13px}
.f-line{font-size:9px;display:flex;align-items:center;gap:9px}
.copy{right:78px;top:31px;font-size:8.4px;text-align:right}
</style>
</head>
<body>
<div class="page">
  <header class="header abs"></header>
  <div class="brand abs"><span class="brand-square"></span><span class="brand-name">Torvel Capital</span></div>
  <div class="contact-top abs">
    <svg width="20" height="16" viewBox="0 0 20 16"><path d="M3 2c2-1 3 0 4 2l-1 2c1 2 3 4 5 5l2-1c2 1 3 2 2 4-1 1-3 2-5 1C6 13 2 8 1 5c0-1 1-2 2-3z" fill="#333"/></svg>
    <div>Desmond Harlow</div><div>555.014.2290</div>
  </div>
  <nav class="nav abs">
    <a class="active" style="width:81px">Home</a><a style="width:80px">About</a><a style="width:87px">Services</a><a style="width:151px">Current Engagements</a><a style="width:159px">Completed Transactions</a><a style="width:85px">Contact</a>
  </nav>

  <div class="hero abs" role="img" aria-label="City skyline photograph with high-rise towers and cranes under a cloudy sky"></div>
  <div class="hero-caption abs">Torvel Capital is an independent investment bank working for buyers in a number of industries.</div>
  <div class="dots abs"><span class="on"></span><span></span><span></span><span></span></div>

  <section class="services abs"></section>
  <h2 class="h2 abs" style="left:80px;top:416px">Services</h2>
  <div class="svc abs" style="left:83px;top:458px"><h3>Strategic Advisory Services</h3><p>Sed ut perspiciatis unde omnis iste natus error sit voluptatem accusantium doloremque laudantium, totam rem aperiam, eaque ipsa quae ab illo inventore veritatis et quasi architecto beatae vitae</p><a>More &gt;&gt;</a></div>
  <div class="svc abs" style="left:261px;top:458px"><h3>Current<br>Engagements</h3><p>Sed ut perspiciatis unde omnis iste natus error sit voluptatem accusantium doloremque laudantium, totam rem aperiam, eaque ipsa quae ab illo inventore veritatis et quasi architecto beatae vitae</p><a>More &gt;&gt;</a></div>
  <div class="svc abs" style="left:439px;top:458px"><h3>Completed<br>Transactions</h3><p>Sed ut perspiciatis unde omnis iste natus error sit voluptatem accusantium doloremque laudantium, totam rem aperiam, eaque ipsa quae ab illo inventore veritatis et quasi architecto beatae vitae</p><a>More &gt;&gt;</a></div>
  <div class="svc abs" style="left:624px;top:458px"><h3>Regulatory<br>Compliance</h3><p>Sed ut perspiciatis unde omnis iste natus error sit voluptatem accusantium doloremque laudantium, totam rem aperiam, eaque ipsa quae ab illo inventore veritatis et quasi architecto beatae vitae</p><a>More &gt;&gt;</a></div>

  <h2 class="welcome-h abs h2">Welcome to <b>Torvel Capital</b></h2>
  <p class="welcome-p abs">Torvel Capital is an independent investment bank working for buyers in a number of industries. We utilize exceptional technology in finding companies to meet our client's search criteria. We will not waste a buyer's time, a seller's time, or our own time.</p>
  <div class="btn abs">LEARN MORE</div>
  <div class="map abs" role="img" aria-label="World map with location markers in North America, Asia and eastern Russia"></div>

  <section class="who abs"></section>
  <h2 class="who-h abs h2">Who <b>We Are</b></h2>
  <div class="tabs abs"><span class="on" style="width:161px">OUR CLIENTS</span><span style="width:128px">OUR PROCESS</span><span style="width:130px">TEAM</span></div>
  <div class="tab-panel abs"></div>
  <p class="tab-text abs">Torvel Capital has a diverse array of clients ranging from multi-billion dollar strategic acquirers to large private equity funds. We will not engage a client as a buyer if we believe there is any chance of them wasting our time or a prospective seller's time.</p>
  <div class="clients abs">
    <span>Norvane</span><span>Kelstra</span><span>Brisk&amp;Co</span><span>Velora Park</span><span>Harwick</span><span>Solenta</span><span>Altura</span><span>Restwell</span><span>Quorvia</span><span>Madoka</span><span>Civic Office</span>
  </div>

  <footer class="footer abs">
    <h4>Contact</h4>
    <svg class="abs" style="left:84px;top:42px" width="16" height="13" viewBox="0 0 16 13"><path d="M8 0 0 7h2v6h4V9h4v4h4V7h2z" fill="#ddd"/></svg>
    <div class="f-addr abs">In nunc augue, egestas commodo pharetra massa. Phasellus sodales.</div>
    <div class="f-line abs" style="left:255px;top:42px"><svg width="13" height="12" viewBox="0 0 20 16"><path d="M3 2c2-1 3 0 4 2l-1 2c1 2 3 4 5 5l2-1c2 1 3 2 2 4-1 1-3 2-5 1C6 13 2 8 1 5c0-1 1-2 2-3z" fill="#ddd"/></svg>555.014.2290</div>
    <div class="f-line abs" style="left:255px;top:68px"><svg width="14" height="10" viewBox="0 0 14 10"><rect x=".5" y=".5" width="13" height="9" fill="none" stroke="#ddd"/><path d="M.5 .5 7 6 13.5 .5" fill="none" stroke="#ddd"/></svg>dharlow@torvelcapital.com</div>
    <div class="copy abs">© 2014 torvelcapital.com. All Rights Reserved</div>
  </footer>
</div>
</body>
</html>
```